4th Generation Family Business Needs a New Card Design!

We are a family owned 4th Generation company. We are based in the Sydney, Australia area and we are desperately in need of a more modern and classy card. We are monumental masons who design, supply & erect lasting memorials throughout cemeteries in Sydney. Our customers are normally in a period of grieving. I have attached logo files that will need to be implemented on the card. Company was established 1935. Australian Owned and Operated. Card needs to be designed to PIXO.com specification.

Target Market(s)

Our target market is based upon people that a grieving for family members that have passed away. We also deal with alot of companies that own and operate cemeteries.

Industry/Entity Type

Business

Contact Information for Business Card

Simon Harcourt, Operations Manager, 0417293086, simon@harcourtmemorials.com.au
Lewis Brantwell, Director, 0491 570 110, lewis@brantwellmemorials.com.au
Phone # 02 5550 1234
Website: www.brantwellmemorials.com.au
Address: Suite 17, 8 Palfrey Lane, West Carlow, Sydney NSW 2156

Font styles to use
Serif
Decorative
Script

Requirements
Must have
• Would like to see the logo nicely implemented with a modern design. Embossed lettering would be a nice additive.

```html
<!DOCTYPE html>
<html lang="en">
<head>
<meta charset="utf-8">
<title>Brantwell Memorials – Business Card</title>
<link rel="stylesheet" href="https://fonts.googleapis.com/css2?family=Montserrat:wght@400;500;600;700&display=swap">
<style>
  :root {
    --gold: #edbe2e;
    --ink: #111111;
    --paper: #ffffff;
    --backdrop: #2b2b2b;
    --muted: #222222;
  }
  * { margin: 0; padding: 0; box-sizing: border-box; }
  html, body { width: 1200px; height: 900px; overflow: hidden; }
  body {
    background: var(--backdrop);
    font-family: "Montserrat", Arial, sans-serif;
    position: relative;
  }
  .card {
    position: absolute;
    left: 280px;
    width: 640px;
    height: 366px;
    border-radius: 20px;
    overflow: hidden;
  }
  .card-shapes { position: absolute; inset: 0; }
  .card--front { top: 64px; background: var(--gold); }
  .card--back { top: 470px; background: var(--paper); }

  .brand-name {
    position: absolute;
    font-family: "Montserrat", Arial, sans-serif;
    font-weight: 700;
    color: var(--ink);
    letter-spacing: 0.12em;
    line-height: 1.15;
    white-space: nowrap;
  }
  .card--front .brand-name {
    left: 0; right: 0; top: 120px;
    font-size: 34px;
    text-align: center;
  }
  .front-web {
    position: absolute;
    right: 30px; top: 280px;
    font-size: 13px;
    color: var(--paper);
    font-weight: 500;
  }
  .front-web strong { font-weight: 700; }

  .card--back .brand-name {
    left: 36px; top: 118px;
    font-size: 24px;
    text-align: left;
  }
  .identity {
    position: absolute;
    right: 34px; top: 44px;
    width: 260px;
    text-align: right;
  }
  .identity-name {
    color: var(--gold);
    font-size: 26px;
    font-weight: 600;
    line-height: 1.1;
    white-space: nowrap;
  }
  .identity-role {
    font-size: 13px;
    color: var(--muted);
    margin-top: 2px;
    padding-bottom: 6px;
    border-bottom: 1px solid var(--ink);
  }
  .identity-address {
    font-size: 12.5px;
    color: var(--muted);
    margin-top: 8px;
    line-height: 1.45;
  }
  .contact-list {
    position: absolute;
    left: 36px; top: 232px;
    width: 300px;
    list-style: none;
    border-top: 1px solid var(--ink);
    padding-top: 8px;
  }
  .contact-item {
    display: flex;
    align-items: center;
    gap: 9px;
    font-size: 13.5px;
    color: var(--muted);
    line-height: 1.5;
    white-space: nowrap;
  }
  .contact-item svg { width: 11px; height: 11px; flex: none; fill: var(--gold); }
  .contact-item strong { color: var(--gold); font-weight: 700; }
</style>
</head>
<body>

<section class="card card--front" aria-label="Card front">
  <svg class="card-shapes" viewBox="0 0 640 366" aria-hidden="true">
    <polygon points="390,306 640,296 640,366 390,366" fill="#ffffff"/>
    <polygon points="0,322 388,322 420,338 640,338 640,366 0,366" fill="#111111"/>
  </svg>
  <div class="brand-name">BRANTWELL<br>MEMORIALS</div>
  <div class="front-web">www.<strong>brantwellmemorials</strong>.com.au</div>
</section>

<section class="card card--back" aria-label="Card back">
  <svg class="card-shapes" viewBox="0 0 640 366" aria-hidden="true">
    <polygon points="440,278 640,278 640,366 420,366" fill="#edbe2e"/>
    <polygon points="0,356 420,356 418,366 0,366" fill="#111111"/>
  </svg>

  <div class="brand-name">BRANTWELL<br>MEMORIALS</div>

  <div class="identity">
    <div class="identity-name">Lewis Brantwell</div>
    <div class="identity-role">Director</div>
    <div class="identity-address">Suite 17, 8 Palfrey Lane<br>West Carlow, Sydney NSW 2156</div>
  </div>

  <ul class="contact-list">
    <li class="contact-item">
      <svg viewBox="0 0 12 12"><rect x="3" y="0" width="6" height="12" rx="1.5"/></svg>
      0491 570 110
    </li>
    <li class="contact-item">
      <svg viewBox="0 0 12 12"><path d="M2 0h3l1 3-2 1.5a7 7 0 0 0 3.5 3.5L9 6l3 1v3a2 2 0 0 1-2 2A10 10 0 0 1 0 2a2 2 0 0 1 2-2z"/></svg>
      02 5550 1234
    </li>
    <li class="contact-item">
      <svg viewBox="0 0 12 12"><path d="M0 2h12v8H0zM1 3l5 3.5L11 3"/></svg>
      lewis@brantwellmemorials.com.au
    </li>
    <li class="contact-item">
      <svg viewBox="0 0 12 12"><circle cx="6" cy="6" r="6"/></svg>
      <span>www.<strong>brantwellmemorials</strong>.com.au</span>
    </li>
  </ul>
</section>

</body>
</html>
```